Business Card Design for my Real Estate Investing Company

This is for a Real Estate Investing Company that will be serving the Las Vegas Valley. Id like the following slogan included: "Building Value Together" I have attached my logo. You will see the color tones I'm interested in..in my logo. I would like the card to be double-sided with a modern, professional look.
Target Market(s)
Homeowners, banks, real estate industry
Industry/Entity Type
Real Estate
Contact Information for Business Card
name: Dale Harwick
position: Managing Member
address: 4821 Corliss Pkwy ste 207-300
Harlow Springs, NV 89990
phone: (702) 555-0143
fax: (702) 555-0187
email: SummitRidgeEstate@hollowmail.test
web: SummitRidgeEstates.test
*At the bottom of the card I would like....
We buy houses for cash....no repairs, no commissions, no fees!
Logo Text
SUMMIT RIDGE ESTATES "Investing in Our Community"
Font styles to use
Other font styles liked:
- Lora
Requirements
Must have
- On the back of the card, i'd like to have my logo large and the following statements:
- Are you considering selling your home? Want a simple, hassle-free transaction? We can help! We buy houses for cash and can close quickly! No need to do any repairs, no realtor commissions, no closing costs.....and no headaches. Let us help you with your real estate needs...!
Nice to have
- multiple colors 2 two tone on front and back

```html
<!DOCTYPE html>
<html lang="en">
<head>
<meta charset="utf-8">
<title>Summit Ridge Estates – Business Card</title>
<link rel="stylesheet" href="https://fonts.googleapis.com/css2?family=Lora:ital,wght@0,400;0,700;1,400&family=Arimo:wght@400&display=swap">
<style>
  :root {
    --bg: #ecebe8;
    --card: #ffffff;
    --blue: #1f7cc4;
    --blue-dark: #0f5fa3;
    --blue-light: #3aa0da;
    --grey: #9a9b9d;
    --ink: #1e1e1e;
    --muted: #555555;
  }
  html, body {
    margin: 0;
    width: 1200px;
    height: 858px;
    overflow: hidden;
    background: var(--bg);
  }
  .canvas {
    position: relative;
    width: 1200px;
    height: 858px;
  }
  .card {
    position: absolute;
    width: 560px;
    height: 320px;
    background: var(--card);
    box-shadow: 0 6px 18px rgba(0,0,0,.18);
    overflow: hidden;
  }
  .card--front { left: 40px; top: 100px; }
  .card--back  { left: 600px; top: 440px; }

  .swoosh { position: absolute; left: 0; top: 0; }

  .brand {
    position: absolute;
    display: flex;
    flex-direction: column;
    align-items: flex-start;
  }
  .brand__row { display: flex; align-items: center; gap: 10px; }
  .brand__mark { width: 20px; height: 20px; background: var(--blue); flex: none; }
  .brand__name {
    font-family: "Lora", serif;
    font-weight: 700;
    color: var(--blue);
    letter-spacing: 1px;
    white-space: nowrap;
  }
  .brand__slogan {
    font-family: "Lora", serif;
    font-style: italic;
    color: var(--muted);
    letter-spacing: 3px;
    margin-top: 6px;
    white-space: nowrap;
  }
  .card--front .brand { left: 30px; top: 28px; }
  .card--front .brand__name { font-size: 22px; }
  .card--front .brand__slogan { font-size: 11px; }

  .contacts {
    position: absolute;
    right: 22px;
    top: 80px;
    margin: 0;
    padding: 0;
    list-style: none;
    font-family: "Arimo", sans-serif;
    font-size: 13px;
    color: var(--ink);
    text-align: right;
    line-height: 20px;
  }
  .contacts li { display: flex; justify-content: flex-end; align-items: center; gap: 8px; white-space: nowrap; }
  .contacts .icon {
    width: 14px; height: 14px; background: var(--blue);
    display: inline-flex; align-items: center; justify-content: center;
  }
  .contacts .icon--none { background: transparent; }

  .person {
    position: absolute;
    left: 34px;
    bottom: 26px;
    font-family: "Lora", serif;
    color: #fff;
  }
  .person__name { font-size: 22px; font-weight: 700; margin: 0; }
  .person__role { font-size: 15px; margin: 2px 0 0; }

  .card--back .brand {
    left: 0; right: 0; top: 92px;
    align-items: center;
  }
  .card--back .brand__name { font-size: 34px; }
  .card--back .brand__slogan { font-size: 13px; margin-top: 10px; }
  .tagline {
    position: absolute;
    left: 0; right: 0; bottom: 30px;
    text-align: center;
    font-family: "Lora", serif;
    font-style: italic;
    font-size: 15px;
    color: var(--blue);
    margin: 0;
  }
</style>
</head>
<body>
<main class="canvas">

  <section class="card card--front" aria-label="Card front">
    <svg class="swoosh" width="560" height="320" viewBox="0 0 560 320" aria-hidden="true">
      <defs>
        <linearGradient id="band" x1="0" y1="0" x2="1" y2="1">
          <stop offset="0" stop-color="#0f5fa3"/>
          <stop offset="1" stop-color="#3aa0da"/>
        </linearGradient>
      </defs>
      <path d="M0,158 C170,214 380,240 560,230 L560,240 C380,252 170,228 0,176 Z" fill="#9a9b9d"/>
      <path d="M0,184 C180,240 390,262 560,252 L560,320 L0,320 Z" fill="url(#band)"/>
    </svg>

    <div class="brand">
      <div class="brand__row">
        <span class="brand__mark"></span>
        <span class="brand__name">SUMMIT RIDGE ESTATES</span>
      </div>
      <span class="brand__slogan">"Building Value Together"</span>
    </div>

    <ul class="contacts">
      <li>(702) 555-0143
        <span class="icon"><svg width="10" height="10" viewBox="0 0 10 10"><path d="M2,1 L4,1 L4.5,3 L3.5,4 C4,5.5 4.5,6 6,6.5 L7,5.5 L9,6 L9,8 C5,9 1,5 2,1 Z" fill="#fff"/></svg></span></li>
      <li>(702) 555-0187
        <span class="icon"><svg width="10" height="10" viewBox="0 0 10 10"><rect x="2" y="1" width="6" height="3" fill="#fff"/><rect x="1" y="4" width="8" height="4" fill="#fff"/></svg></span></li>
      <li>SummitRidgeEstate@hollowmail.test
        <span class="icon"><svg width="10" height="10" viewBox="0 0 10 10"><rect x="1" y="2" width="8" height="6" fill="#fff"/><path d="M1,2 L5,5.5 L9,2" stroke="#1f7cc4" fill="none"/></svg></span></li>
      <li>SummitRidgeEstates.test
        <span class="icon"><svg width="10" height="10" viewBox="0 0 10 10"><circle cx="5" cy="5" r="3.8" stroke="#fff" fill="none"/><path d="M1.2,5 H8.8 M5,1.2 V8.8" stroke="#fff"/></svg></span></li>
      <li>4821 Corliss Pkwy ste 207-300
        <span class="icon"><svg width="10" height="10" viewBox="0 0 10 10"><path d="M5,9.5 C2,6 2,5 2,4 A3,3 0 0 1 8,4 C8,5 8,6 5,9.5 Z" fill="#fff"/><circle cx="5" cy="4" r="1.1" fill="#1f7cc4"/></svg></span></li>
      <li>Harlow Springs, NV 89990 <span class="icon icon--none"></span></li>
    </ul>

    <div class="person">
      <p class="person__name">Dale Harwick</p>
      <p class="person__role">Managing Member</p>
    </div>
  </section>

  <section class="card card--back" aria-label="Card back">
    <div class="brand">
      <div class="brand__row">
        <span class="brand__mark"></span>
        <span class="brand__name">SUMMIT RIDGE ESTATES</span>
      </div>
      <span class="brand__slogan">"Building Value Together"</span>
    </div>
    <p class="tagline">We buy houses for cash....no repairs, no commissions, no fees!</p>
  </section>

</main>
</body>
</html>
```